KELBRIDGE PAINTING

We are a painting company. We paint residential, commercial and strata jobs. I need the website to be very sharp, neat and elegant. I've attached our logo. the Logo needs to be embossed as a gold color and the background like a Matt black. I need these tabs:

• HOME • ABOUT US • SERVICES • TESTIMONIALS • SHOWCASE • CONTACT US

Be creative and innovative in your style.
take this as an example to just get the gist of what I'm expecting. If you can better it then the job is yours!

http://rickhalvorpainting.com.au/contact.html

I look forward to seeing your artwork :)

#These are the links to my logo in PSD format.

https://www.filevaultzy.com/s/qwertplk83nd7ha/Kelbridge%20Painting%20Luxury%20Gold.rar

https://www.filevaultzy.com/sh/bzuyrak2m5wqp9/QoPL7-xvMn

Painting

• Making the Logo embossed like the artworks i have attached is definitely a necessity.

Can you let me know if this is possible to apply to the website.

thank you

```html
<!DOCTYPE html>
<html lang="en">
<head>
<meta charset="utf-8">
<title>Kelbridge Painting</title>
<link href="https://fonts.googleapis.com/css2?family=Source+Sans+3:ital,wght@0,400;0,600;0,700;1,400&display=swap" rel="stylesheet">
<style>
:root{
  --ink:#1e232b;
  --gold:#f0c050;
  --gold-deep:#d4a010;
  --gold-mid:#e2b040;
  --gold-soft:#ecc060;
  --gold-pale:#f5d9a0;
  --slate-1:#4a4f57;
  --slate-2:#6b7078;
  --slate-3:#9a9da1;
  --footer:#464a50;
  --white:#ffffff;
  --icon:#d2d3d5;
}
*{margin:0;padding:0;box-sizing:border-box}
html,body{width:1040px;height:1200px;overflow:hidden;background:var(--ink)}
body{font-family:"Source Sans 3",sans-serif;color:var(--white);position:relative}
.site-header{position:absolute;left:0;top:0;width:1040px;height:80px;background:var(--ink);border-bottom:1px solid var(--gold-mid);z-index:3}
.phone{position:absolute;right:144px;top:16px;display:flex;align-items:center;gap:8px;color:var(--gold);font-weight:700;font-size:19px;letter-spacing:.3px}
.main-nav{position:absolute;right:143px;top:55px;display:flex;gap:26px;font-size:12.5px;font-weight:600;letter-spacing:.6px}
.main-nav a{color:var(--white);text-decoration:none}
.main-nav a.active{color:var(--gold)}
.logo-disc{position:absolute;left:144px;top:18px;width:100px;height:100px;border-radius:50%;background:var(--ink);z-index:5}
.brand-bar{position:absolute;left:240px;top:81px;width:440px;height:35px;background:linear-gradient(90deg,#f3d36a,#e9c04a 60%,#f1cf63);display:flex;align-items:center;padding-left:14px;z-index:4;color:var(--ink)}
.brand-name{font-weight:700;font-size:20px;letter-spacing:1.2px}
.brand-divider{width:1px;height:18px;background:#9a7a20;margin:0 12px}
.brand-tagline{font-style:italic;font-size:16px}
.hero{position:absolute;left:0;top:81px;width:1040px;height:391px;background:linear-gradient(180deg,#6e5a48 0%,#8a6a50 35%,#6a4630 60%,#b8a08c 85%,#c9b6a6 100%)}
.slider-dots{position:absolute;right:144px;top:107px;display:flex;gap:8px;z-index:4}
.slider-dots span{width:8px;height:8px;background:#3b3f45}
.slider-dots span.on{background:var(--gold)}
.accent-tl{position:absolute;left:143px;top:291px;width:48px;height:47px;background:var(--gold-mid)}
.accent-br{position:absolute;left:576px;top:340px;width:144px;height:88px;background:var(--gold-mid)}
.caption{position:absolute;left:152px;top:299px;width:552px;height:120px;background:var(--ink);padding:16px 0 0 31px;font-size:40px;line-height:44px;color:var(--white)}
.caption-tab{position:absolute;left:674px;top:299px;width:30px;height:5px;background:var(--slate-3)}
.stripe{position:absolute;left:0;width:1040px;height:8px;display:flex}
.stripe span{height:8px}
.services{position:absolute;left:143px;top:510px;width:760px}
.services h1{font-size:39px;font-weight:700;color:var(--gold);line-height:48px}
.service-grid{display:grid;grid-template-columns:256px 256px 248px;row-gap:42px;margin-top:44px}
.service h2{font-size:24.5px;line-height:24px;font-weight:700;color:var(--gold-mid);text-transform:uppercase;letter-spacing:.2px}
.service p{margin-top:14px;font-size:13.4px;line-height:24px;font-weight:600;width:225px}
.site-footer{position:absolute;left:0;top:1144px;width:1040px;height:56px;background:var(--footer)}
.copyright{position:absolute;left:145px;top:17px;font-size:11.5px;font-weight:600}
.social{position:absolute;left:748px;top:16px;display:flex;gap:14px}
.social span{width:26px;height:26px;border-radius:50%;background:var(--icon)}
</style>
</head>
<body>
<header class="site-header">
  <div class="phone">
    <svg width="18" height="18" viewBox="0 0 24 24" aria-hidden="true"><path fill="#f0c050" d="M6.6 10.8c1.4 2.8 3.8 5.1 6.6 6.6l2.2-2.2c.3-.3.7-.4 1-.2 1.1.4 2.3.6 3.6.6.6 0 1 .4 1 1V20c0 .6-.4 1-1 1C10.6 21 3 13.4 3 4c0-.6.4-1 1-1h3.5c.6 0 1 .4 1 1 0 1.3.2 2.5.6 3.6.1.3 0 .7-.2 1z"/></svg>
    1300 47 19 52
  </div>
  <nav class="main-nav">
    <a class="active" href="#">HOME</a><a href="#">ABOUT US</a><a href="#">SERVICES</a><a href="#">TESTIMONIALS</a><a href="#">SHOWCASE</a><a href="#">CONTACT US</a>
  </nav>
</header>
<div class="logo-disc"></div>
<div class="brand-bar"><span class="brand-name">KELBRIDGE PAINTING</span><span class="brand-divider"></span><span class="brand-tagline">Painting Australia Everyday!</span></div>
<section class="hero" role="img" aria-label="Photo of a modern living room with a brown and cream leather sectional sofa"></section>
<div class="slider-dots"><span></span><span></span><span></span><span class="on"></span></div>
<div class="accent-tl"></div>
<div class="accent-br"></div>
<div class="caption">We paint residential,<br>commercial and strata jobs</div>
<div class="caption-tab"></div>
<div class="stripe" style="top:472px">
  <span style="width:249px;background:var(--ink)"></span><span style="width:71px;background:var(--slate-1)"></span><span style="width:78px;background:var(--slate-2)"></span><span style="width:124px;background:var(--slate-3)"></span><span style="width:104px;background:var(--gold-deep)"></span><span style="width:71px;background:var(--gold-mid)"></span><span style="width:78px;background:var(--gold-soft)"></span><span style="width:265px;background:var(--gold-pale)"></span>
</div>
<main class="services">
  <h1>Our Services</h1>
  <div class="service-grid">
    <article class="service"><h2>Commercial<br>Painting</h2><p>Lorem ipsum dolor sit amet, consectetur adipiscing elit. Quantum Aristoxeni ingenium consumptum videmus in musicis? Nihil enim hoc differt. Re mihi non aeque satisfacit, et quidem locis pluribus.</p></article>
    <article class="service"><h2>Color<br>Consulting</h2><p>Lorem ipsum dolor sit amet, consectetur adipiscing elit. Quantum Aristoxeni ingenium consumptum videmus in musicis? Nihil enim hoc differt. Re mihi non aeque satisfacit, et quidem locis pluribus.</p></article>
    <article class="service"><h2>Fence<br>Painting</h2><p>Lorem ipsum dolor sit amet, consectetur adipiscing elit. Quantum Aristoxeni ingenium consumptum videmus in musicis? Nihil enim hoc differt. Re mihi non aeque satisfacit, et quidem locis pluribus.</p></article>
    <article class="service"><h2>Exterior Timber<br>Maintenance</h2><p>Lorem ipsum dolor sit amet, consectetur adipiscing elit. Quantum Aristoxeni ingenium consumptum videmus in musicis? Nihil enim hoc differt. Re mihi non aeque satisfacit, et quidem locis pluribus.</p></article>
    <article class="service"><h2>Special<br>Finishes</h2><p>Lorem ipsum dolor sit amet, consectetur adipiscing elit. Quantum Aristoxeni ingenium consumptum videmus in musicis? Nihil enim hoc differt. Re mihi non aeque satisfacit, et quidem locis pluribus.</p></article>
    <article class="service"><h2>Spray<br>Painting</h2><p>Lorem ipsum dolor sit amet, consectetur adipiscing elit. Quantum Aristoxeni ingenium consumptum videmus in musicis? Nihil enim hoc differt. Re mihi non aeque satisfacit, et quidem locis pluribus.</p></article>
  </div>
</main>
<div class="stripe" style="top:1136px">
  <span style="width:265px;background:var(--gold-pale)"></span><span style="width:79px;background:var(--gold-soft)"></span><span style="width:70px;background:var(--gold-mid)"></span><span style="width:106px;background:var(--gold-deep)"></span><span style="width:122px;background:var(--slate-3)"></span><span style="width:78px;background:var(--slate-2)"></span><span style="width:71px;background:var(--slate-1)"></span><span style="width:249px;background:var(--ink)"></span>
</div>
<footer class="site-footer">
  <p class="copyright">Copyright @ 2013 Kelbridge Painting. All rights reserved.</p>
  <div class="social"><span></span><span></span><span></span><span></span></div>
</footer>
</body>
</html>
```